Business Card Design for Software Development Company

I am looking for a business card design the incorporates my new logo (attached below).

Key information to include:
Name: Martin Quelbrook
Title: CEO
Email: martin@brightwellcivic.example
Phone: 555-218-9403
Website: www.brightwellcivic.example

NOTE: This design should be easy to edit so that we can order cards for different members of our team.

```html
<!DOCTYPE html>
<html lang="en">
<head>
<meta charset="utf-8">
<title>BrightwellLabs – Business Card</title>
<link href="https://fonts.googleapis.com/css2?family=Montserrat:wght@400;500;700;800&display=swap" rel="stylesheet">
<style>
  :root {
    --backdrop: #3a3a3a;
    --card-white: #ffffff;
    --slate: #6e7899;
    --slate-deep: #5f6888;
    --navy: #2f3550;
    --orange: #e8843f;
    --ink: #2b2b2b;
  }
  * { margin: 0; padding: 0; box-sizing: border-box; }
  html, body {
    width: 1200px; height: 1200px; overflow: hidden;
    background: var(--backdrop);
    font-family: "Montserrat", Arial, sans-serif;
  }
  .canvas {
    width: 1200px; height: 1200px;
    display: flex; flex-direction: column; align-items: center; justify-content: center;
    gap: 60px;
  }
  .card {
    position: relative;
    width: 860px; height: 491px;
    border-radius: 28px;
    overflow: hidden;
    box-shadow: 0 12px 30px rgba(0,0,0,.45);
  }
  .brand { display: flex; align-items: center; gap: 14px; }
  .brand-mark { width: 34px; height: 34px; background: var(--orange); flex: none; }
  .brand-text { display: flex; flex-direction: column; align-items: flex-end; white-space: nowrap; }
  .brand-name { font-weight: 700; line-height: 1; color: var(--navy); }
  .brand-tag { font-weight: 700; text-transform: uppercase; color: var(--navy); letter-spacing: .06em; }

  /* Back side */
  .card-back {
    background: var(--slate);
    display: flex; align-items: center; justify-content: center;
  }
  .card-back .brand-name { font-size: 70px; color: var(--slate-deep); }
  .card-back .brand-tag { font-size: 11px; color: var(--slate-deep); margin-top: 6px; }
  .card-back .brand-mark { width: 44px; height: 44px; }

  /* Front side */
  .card-front { background: var(--card-white); }
  .card-front .waves { position: absolute; inset: 0; }
  .card-front .brand { position: absolute; left: 84px; top: 206px; gap: 10px; }
  .card-front .brand-name { font-size: 30px; }
  .card-front .brand-tag { font-size: 6px; margin-top: 4px; }
  .card-front .brand-mark { width: 20px; height: 20px; }
  .divider {
    position: absolute; left: 408px; top: 112px;
    width: 2px; height: 150px; background: var(--orange);
  }
  .contact { position: absolute; left: 430px; top: 104px; color: var(--ink); white-space: nowrap; }
  .person-name { font-size: 28px; font-weight: 800; color: var(--orange); line-height: 1.1; }
  .person-title { font-size: 17px; font-weight: 400; margin: 4px 0 6px; }
  .contact-line { display: flex; align-items: center; gap: 10px; font-size: 16px; line-height: 1.6; }
  .contact-line svg { width: 14px; height: 14px; flex: none; fill: var(--orange); }
</style>
</head>
<body>
<main class="canvas">

  <section class="card card-back" aria-label="Card back">
    <div class="brand">
      <span class="brand-mark"></span>
      <div class="brand-text">
        <span class="brand-name">BrightwellLabs</span>
        <span class="brand-tag">A division of Brightwell Civic</span>
      </div>
    </div>
  </section>

  <section class="card card-front" aria-label="Card front">
    <svg class="waves" viewBox="0 0 860 491" preserveAspectRatio="none" aria-hidden="true">
      <path d="M0,491 L0,440 C120,372 260,352 430,348 C620,344 800,322 860,252 L860,491 Z" fill="var(--slate)"/>
      <path d="M40,452 C150,388 280,364 440,358 C630,352 800,334 860,270" fill="none" stroke="var(--card-white)" stroke-width="2.5"/>
      <path d="M420,339 C620,327 800,307 860,222 L860,234 C800,320 620,338 420,341 Z" fill="var(--slate)"/>
      <path d="M380,330 C600,315 790,290 860,170 L860,210 C790,308 600,328 380,330 Z" fill="var(--orange)"/>
    </svg>

    <div class="brand">
      <span class="brand-mark"></span>
      <div class="brand-text">
        <span class="brand-name">BrightwellLabs</span>
        <span class="brand-tag">A division of Brightwell Civic</span>
      </div>
    </div>

    <div class="divider"></div>

    <div class="contact">
      <p class="person-name">Martin Quelbrook</p>
      <p class="person-title">CEO</p>
      <p class="contact-line">
        <svg viewBox="0 0 24 24"><path d="M6.6 10.8a15 15 0 0 0 6.6 6.6l2.2-2.2c.3-.3.7-.4 1-.2 1.1.4 2.3.6 3.6.6.6 0 1 .4 1 1V20c0 .6-.4 1-1 1A17 17 0 0 1 3 4c0-.6.4-1 1-1h3.5c.6 0 1 .4 1 1 0 1.3.2 2.5.6 3.6.1.3 0 .7-.2 1z"/></svg>
        555-218-9403
      </p>
      <p class="contact-line">
        <svg viewBox="0 0 24 24"><path d="M2 5h20v14H2z"/></svg>
        martin@brightwellcivic.example
      </p>
      <p class="contact-line">
        <svg viewBox="0 0 24 24"><circle cx="12" cy="12" r="10"/></svg>
        www.brightwellcivic.example
      </p>
    </div>
  </section>

</main>
</body>
</html>
```